3D abstract logo Construction, Kitchen and Bath design and Project Management Business Card Design

I want a 3d abstract logo for a new General Construction, Kitchen and Bath design and Project Management Company located at Philadelphia PA, we want to put our logo in the white color trucks too. I want to look professional and serious at the same time look like an architect design and the warm originals color that make you feel in a nice decorated home, I like the colors trend in this link:
http://www.quellmark.example/qm/ggs/pageeditor.aspx?alt_doc_id=RT41K-M9B33-2W5&doc_id=5913046628&pf_id=D4H

I was thinking about a roof and the PA font could have square shape or like wood framing with two tones of the brick color black and creamy yellow color.... Also I like the keystone Idea like the modification or the Ridgeline Parkway logo but curvy at the top

The final design should communicate big company (because we want to grow), responsible, professional and organized that really care about our customers and give them everything they need... plan and design, excellent labor and Project Management
Updates

I doesn't have to be 3d

Reason: I haven't received enough options...

Please stick with the warm tones shown in the image001 attached I like spicy cinnamon instead a cold wine or brick color and also the cream yellowish tones added

Hello designers, please use only the idea and colors of the image001 I don't want to be stick with a house logo because I do commercial construction too so I prefer work around the keystone idea maybe leaving the style of the PA.
I'd like the base tone on the card dark like first option and you can send me a white option too.

Please send me your ideas as soon as possible 

Thank you so much!

Target Market(s)

Builders, State, commercial business owners, Property owners or Real State and Property Management Companies

Industry/Entity Type

Architect

Contact Information for Business Card

RK Buildworks LLC
“Your project is our business”
Lorna Vasquel Eng.
President
Commercial & Residential General Construction
Kitchen & Bath Design | Project Management
Phone: 555-304-7718 | Fax: 555-304-7719 Cell: 555-862-3097
lorna@rkbuildworks.example

```html
<!DOCTYPE html>
<html lang="en">
<head>
<meta charset="utf-8">
<title>RK Buildworks – Business Card</title>
<link rel="stylesheet" href="https://fonts.googleapis.com/css2?family=Open+Sans:ital,wght@0,400;0,700;1,400&family=Arimo:wght@400&display=swap">
<style>
  :root {
    --cinnamon: #6e1f1c;
    --cream: #f3ead6;
    --tan: #c9a46a;
    --rose: #c98a7e;
    --backdrop: #e8e2d8;
    --ink-light: #fbf5ea;
  }
  * { margin: 0; padding: 0; box-sizing: border-box; }
  html, body { width: 1200px; height: 870px; overflow: hidden; }
  body { background: var(--backdrop); position: relative; font-family: "Open Sans", sans-serif; }

  .card { position: absolute; box-shadow: 0 6px 18px rgba(0,0,0,.18); overflow: hidden; }

  /* Back of card */
  .card-back {
    left: 70px; top: 150px; width: 340px; height: 595px;
    background: var(--cinnamon); color: var(--ink-light); text-align: center;
  }
  .brand-name {
    position: absolute; top: 260px; left: 0; right: 0;
    font-size: 30px; font-weight: 700; letter-spacing: 2px; color: var(--cream);
  }
  .tagline {
    position: absolute; top: 318px; left: 0; right: 0;
    font-family: "Arimo", sans-serif; font-size: 21px;
  }
  .website {
    position: absolute; top: 470px; left: 0; right: 0;
    font-family: "Arimo", sans-serif; font-size: 17px;
  }

  /* Front of card */
  .card-front { left: 460px; top: 290px; width: 680px; height: 389px; }
  .card-front svg { position: absolute; inset: 0; }
  .front-text { position: absolute; inset: 0; color: var(--ink-light); }
  .person-name {
    position: absolute; left: 42px; top: 30px;
    font-size: 40px; font-weight: 700; letter-spacing: 1px; line-height: 1;
  }
  .person-title {
    position: absolute; left: 44px; top: 80px;
    font-size: 22px; font-style: italic;
  }
  .services {
    position: absolute; left: 44px; top: 128px; width: 430px;
    font-size: 19px; line-height: 1.3;
  }
  .contacts {
    position: absolute; left: 46px; top: 232px;
    font-family: "Arimo", sans-serif; font-size: 16px;
    display: grid; grid-template-columns: 96px auto; row-gap: 9px;
  }
  .front-brand {
    position: absolute; left: 500px; top: 356px; width: 120px; text-align: center;
    font-size: 13px; font-weight: 700; color: var(--cinnamon);
  }
</style>
</head>
<body>

  <section class="card card-back">
    <div class="brand-name">RK BUILDWORKS</div>
    <p class="tagline">Your project is our business</p>
    <p class="website">www.rkbuildworks.example</p>
  </section>

  <section class="card card-front">
    <svg width="680" height="389" viewBox="0 0 680 389" aria-hidden="true">
      <rect class="card-ground" width="680" height="389" fill="var(--cream)"/>
      <path class="stripe-outer" d="M0 0 H650 A404 404 0 0 1 494 389 H0 Z" fill="none"/>
      <circle class="stripe stripe-tan-wide" cx="250" cy="100" r="404" fill="none" stroke="var(--tan)" stroke-width="4"/>
      <circle class="stripe stripe-rose" cx="250" cy="100" r="392" fill="none" stroke="var(--rose)" stroke-width="5"/>
      <circle class="stripe stripe-tan" cx="250" cy="100" r="380" fill="none" stroke="var(--tan)" stroke-width="6"/>
      <path class="panel-dark" d="M0 0 H604 A368 368 0 0 1 478 389 H0 Z" fill="var(--cinnamon)"/>
      <circle class="brand-dot" cx="560" cy="290" r="56" fill="var(--cinnamon)"/>
    </svg>
    <div class="front-text">
      <h1 class="person-name">LORNA VASQUEL</h1>
      <p class="person-title">Eng. President</p>
      <p class="services">Commercial &amp; Residential General Construction Kitchen &amp; Bath Design</p>
      <div class="contacts">
        <span>Phone:</span><span>555-304-7718</span>
        <span>Fax:</span><span>555-304-7719</span>
        <span>Cell:</span><span>555-862-3097</span>
        <span>Email:</span><span>lorna@rkbuildworks.example</span>
      </div>
      <div class="front-brand">RK BUILDWORKS</div>
    </div>
  </section>

</body>
</html>
```